Webdesign for a business that converts shops into apps. UPDATE BRIEF

We want a creative/professional design for our new business Vorbo.

Vorbo is a service that can deliver instant apps for quillora shops. So every shop owner can have its own app for selling to there customers.

We are open for your interpretation of the design. We think it could be intersting doing an onepage design for this. But thats not set in stones offcourse.

We need several section:
top section
some facts abt the service and maybe our company
price table
some customer review
functionalitys of the app (in a nice way shown)
Section showing screens of a demo shop.
footer with ccdetails, socialmedia, newsletter

I have been playing abit myself with a theme, but no development/designer experience. And we really need a very professional and custom look.

Ps. we are an ecommerce company so if we find any good designer here, we will have enough work for you.

Some competitors in this field;

http://shrt.example/k7Tq2Zw
http://shrt.example/p3Nx9Ld

Here is a design we like
http://brelunoweb.example/

Hoping for some great concepts!

Kind Regards and good luck!

Some screenshots which can be used for app demo;

UPDATE BRIEF

We would like to add a section for features of the app.
We would like to show a zelphone screen and all the most important features of the app and when clicking every feature the screen would change or the feature intened would be high lighted in some way.

The features and any content and info abt that can be used from
https://www.tovexa.example/features.html/

We need an how it works section aswell in the design, also that can be used content from here
https://www.tovexa.example/how-it-works/

Tovexa is our partner, so there work way and features are same as ours. We just want it in a different 'look and feel/design)

Reason: Getting very few good design at the moment. Same designers seem to be responding whith 5 designs at a time of low quality.

Target Market(s)

quillora webshop

Industry/Entity Type

Business

Number of Pages Required

1 page

Font styles to use
Sans Serif

Colors
0355a3
3176b5
85acd3
85cae6
33a6d7
0392cd
f59195
33b8a4

Requirements
Must have
• a creative and custom look, not a copied theme vibe.
Nice to have
• it would be nice if the entire design has a nice flow goinf through the site. The customers experience should be on point.
Should not have
• boring static experience

```html
<!DOCTYPE html>
<html lang="en">
<head>
<meta charset="utf-8">
<title>Vorbo – Apps for Quillora shops</title>
<link href="https://fonts.googleapis.com/css2?family=Open+Sans:wght@400;600;700&family=Questrial&display=swap" rel="stylesheet">
<style>
:root{
  --blue-dark:#0355a3;
  --blue:#3176b5;
  --blue-light:#85acd3;
  --sky:#33a6d7;
  --sky-deep:#0392cd;
  --teal:#33b8a4;
  --red:#f05a5f;
  --text:#444;
  --muted:#9a9a9a;
  --line:#e3e3e3;
  --grey-bg:#efefef;
  --soft-bg:#f6f6f6;
  --dark:#2b2b2b;
}
*{box-sizing:border-box;margin:0;padding:0}
html,body{width:1200px;height:4467px;overflow:hidden}
body{font-family:"Open Sans",Arial,sans-serif;color:var(--text);background:#fff;position:relative}
section,header,footer{position:relative;width:1200px;overflow:hidden}
.title{position:absolute;left:0;width:1200px;text-align:center;font-family:"Questrial",sans-serif;font-size:44px;letter-spacing:1px;font-weight:400}
.title.teal{color:var(--teal)}
.title.blue{color:var(--blue-dark)}

/* header */
.site-header{height:119px}
.brand{position:absolute;left:130px;top:28px;font-family:"Open Sans",sans-serif;font-weight:600;font-size:52px;color:var(--blue-dark);letter-spacing:-1px;line-height:1}
.nav{position:absolute;right:130px;top:62px;display:flex;gap:28px;font-size:14px;color:#555}
.nav .active{color:var(--red);position:relative}
.nav .home-ico{position:absolute;left:8px;top:-17px}

/* hero */
.hero{height:497px}
.hero-photo{position:absolute;inset:0;background:linear-gradient(90deg,#8b8f96 0%,#b9b6b1 30%,#a49d96 55%,#5e5a57 80%,#3d3b3a 100%)}
.hero-copy{position:absolute;left:690px;top:268px;width:376px;text-align:right;color:#fff;font-size:34px;line-height:40px;font-weight:400}
.hero-copy b{font-weight:700}
.btn{display:inline-block;font-size:13px;color:#fff;height:36px;line-height:36px;padding:0 22px;border-radius:2px}
.btn-dark{background:#3b3b3b}
.btn-blue{background:var(--blue-dark)}
.hero-btns{position:absolute;right:134px;top:368px;display:flex;gap:14px}
.hero-arrow{position:absolute;top:236px}

/* welcome */
.welcome{height:411px;border-bottom:1px solid var(--line)}
.welcome .title{top:62px}
.lead{position:absolute;left:150px;width:900px;top:113px;text-align:center;font-size:14px;line-height:21px;color:#666}
.facts{position:absolute;left:130px;top:200px;width:940px;display:flex;justify-content:space-between}
.fact{width:210px;text-align:center}
.fact svg{display:block;margin:0 auto 14px}
.fact h3{font-size:21px;font-weight:400;color:var(--blue-dark);margin-bottom:6px}
.fact p{font-size:11px;line-height:15px;color:var(--muted)}

/* pricing */
.pricing{height:492px}
.pricing .title{top:66px}
.plans{position:absolute;left:131px;top:140px;display:flex;gap:30px}
.plan{width:292px;height:292px;border:1px solid #ddd;text-align:center;padding-top:22px}
.plan h3{font-size:24px;color:var(--blue-dark);font-weight:600;line-height:1}
.price{font-size:44px;font-weight:700;color:#333;line-height:50px}
.price small{font-size:20px;font-weight:400;vertical-align:4px}
.price em{font-style:normal;font-size:12px;font-weight:400;color:#777}
.plan ul{list-style:none;margin:8px 28px 0}
.plan li{font-size:10px;color:#666;border-bottom:1px solid var(--line);height:28px;line-height:28px}
.btn-outline{display:inline-block;margin-top:26px;border:1px solid var(--teal);color:var(--teal);font-size:14px;height:44px;line-height:44px;width:130px}

/* reviews */
.reviews{height:452px;background:var(--grey-bg)}
.reviews .title{top:58px}
.review-list{position:absolute;left:125px;top:137px;display:flex;gap:18px}
.review{width:304px}
.review-card{position:relative;background:#fff;height:166px;padding:22px 20px 0 28px;font-size:11px;line-height:17px;color:#777}
.review-card .q{position:absolute;left:14px;top:16px;font-size:34px;color:#bbb;font-family:Georgia,serif}
.review-card p{padding-left:18px}
.review-card::after{content:"";position:absolute;right:0;bottom:-20px;border-top:20px solid #fff;border-left:20px solid transparent}
.reviewer{display:flex;justify-content:flex-end;align-items:center;gap:8px;margin-top:6px;padding-right:36px;font-size:11px;color:#333}
.reviewer small{color:#888;font-size:9px}
.stars{color:#f5a623;font-size:10px;letter-spacing:1px;display:block;line-height:10px}
.avatar{width:30px;height:34px;background:linear-gradient(180deg,#c8b5a4,#8a7a6d)}
.dot-row{position:absolute;top:379px;left:0;width:1200px;display:flex;justify-content:center;gap:14px}
.dot-row i{width:8px;height:8px;border-radius:50%;background:#c6c6c6}
.dot-row i.on{background:var(--sky)}

/* features */
.features{height:456px}
.features .title{top:64px}
.feature-grid{position:absolute;left:132px;top:146px;width:960px;display:grid;grid-template-columns:repeat(3,328px);row-gap:40px}
.feature{display:flex;gap:14px}
.feature svg{flex:none;margin-top:4px}
.feature h3{font-size:19px;font-weight:400;color:#333;line-height:24px}
.feature p{font-size:10px;color:var(--muted);line-height:14px}

/* functionality */
.functions{height:616px;background:var(--soft-bg)}
.functions .title{top:62px}
.app-shot{position:absolute;left:200px;top:150px;width:270px;height:390px;border-radius:40px;transform:rotate(-22deg);background:linear-gradient(160deg,#fafafa 0 10%,#e9e9e9 50%,#cfcfcf);box-shadow:0 16px 30px rgba(0,0,0,.12)}
.app-shot::before{content:"";position:absolute;left:22px;top:54px;right:22px;bottom:54px;background:linear-gradient(180deg,#fff,#f1f1f1 70%,#e65b2a 70% 74%,#f7f7f7 74%)}
.steps{position:absolute;left:527px;top:183px;width:540px}
.step{margin-bottom:48px}
.step h3{font-family:"Questrial",sans-serif;font-size:24px;font-weight:400;color:var(--blue);margin-bottom:6px}
.step p{font-size:11px;line-height:17px;color:#777}

/* demo */
.demo{height:286px}
.demo-photo{position:absolute;inset:0;background:linear-gradient(90deg,#575757 0%,#7c7c7c 35%,#5d5d5d 60%,#8a8681 80%,#4a4a4a 100%)}
.demo-label{position:absolute;left:0;width:1200px;top:86px;text-align:center;color:#fff;font-family:"Questrial",sans-serif;font-size:40px}
.play{position:absolute;left:576px;top:137px}

/* screens */
.screens{height:676px}
.side-shot{position:absolute;top:125px;width:250px;height:380px;background:linear-gradient(180deg,#ffffff,#eeeeee)}
.side-shot.left{left:170px;-webkit-mask-image:linear-gradient(90deg,transparent,#000 70%);mask-image:linear-gradient(90deg,transparent,#000 70%)}
.side-shot.right{left:765px;-webkit-mask-image:linear-gradient(270deg,transparent,#000 70%);mask-image:linear-gradient(270deg,transparent,#000 70%)}
.phone{position:absolute;left:476px;top:74px;width:250px;height:530px;border-radius:36px;background:#1a1a1a}
.phone-screen{position:absolute;left:18px;top:68px;width:214px;height:390px;background:linear-gradient(180deg,#f7f7f7 0 40px,#ffffff 40px 46%,#eaeaea 46% 50%,#ffffff 50%)}
.phone-btn{position:absolute;left:105px;top:478px;width:40px;height:40px;border-radius:50%;border:2px solid #333}
.car-arrow{position:absolute;top:290px}

/* newsletter */
.newsletter{height:179px;background:var(--grey-bg)}
.newsletter .title{top:38px;font-size:42px}
.signup{position:absolute;left:313px;top:100px;display:flex;gap:20px}
.field{width:218px;height:40px;background:#fff;border:1px solid #ddd;font-size:12px;color:#888;padding-left:14px;line-height:38px}
.subscribe{width:98px;height:40px;background:var(--teal);color:#fff;font-size:12px;font-weight:700;text-align:center;line-height:40px}

/* footer */
.site-footer{height:283px}
.col{position:absolute;top:26px}
.col h4{font-size:15px;font-weight:400;color:#333;margin-bottom:12px}
.col p,.col li{font-size:10px;line-height:17px;color:#777;list-style:none}
.col li::before{content:"› ";color:#aaa}
.links{display:flex;gap:36px}
.social{display:flex;gap:8px}
.social i{width:26px;height:26px;border-radius:50%;background:#5a5a5a}
.foot-rule{position:absolute;left:130px;width:940px;top:222px;border-top:1px solid var(--line)}
.copy{position:absolute;left:134px;top:240px;font-size:10px;color:#555}
.to-top{position:absolute;left:1036px;top:233px}
</style>
</head>
<body>

<header class="site-header">
  <div class="brand">Vorbo</div>
  <nav class="nav">
    <span class="active">
      <svg class="home-ico" width="12" height="10" viewBox="0 0 12 10"><path d="M6 0L0 5h2v5h3V7h2v3h3V5h2z" fill="#f05a5f"/></svg>Home</span>
    <span>About</span><span>Services</span><span>Pricing</span><span>Reviews</span><span>App</span><span>Screens &amp; Demo</span><span>Support</span>
  </nav>
</header>

<section class="hero">
  <div class="hero-photo" role="img" aria-label="Photo of a hand holding a smartphone showing a shop app, in front of a blurred store interior"></div>
  <svg class="hero-arrow" style="left:22px" width="16" height="28" viewBox="0 0 16 28"><path d="M14 2L3 14l11 12" stroke="#fff" stroke-width="3" fill="none"/></svg>
  <svg class="hero-arrow" style="left:1160px" width="16" height="28" viewBox="0 0 16 28"><path d="M2 2l11 12L2 26" stroke="#fff" stroke-width="3" fill="none"/></svg>
  <div class="hero-copy"><b>Direct</b> meer omzet met<br>een Quillora app</div>
  <div class="hero-btns"><span class="btn btn-dark">Learn More</span><span class="btn btn-blue">Get App</span></div>
</section>

<section class="welcome">
  <h2 class="title teal">WELCOME</h2>
  <p class="lead">Maecenas consectetur risus sed commodo consectetur. Fusce eleifend nisi vitae elit malesuada, eu pretium turpis tristique. Integer non mollis dui. Suspendisse volutpat dui et lectus pulvinar, eu cursus libero tempor.</p>
  <div class="facts">
    <div class="fact">
      <svg width="56" height="56" viewBox="0 0 56 56" fill="none" stroke="#0355a3" stroke-width="2.5"><path d="M10 46l22-22M36 8a10 10 0 0 0 12 12l-6 6-12-12z"/><path d="M10 10l10 10M8 14l6-6M36 36l10 10-4 4-10-10"/></svg>
      <h3>Easy setup</h3><p>Donec odio nulla, ultrices eget consequat id, blandit eu dui. Morbi accumsan lorem quis maximus mattis.</p>
    </div>
    <div class="fact">
      <svg width="56" height="56" viewBox="0 0 56 56" fill="none" stroke="#0355a3" stroke-width="2.5"><rect x="16" y="4" width="24" height="48" rx="4"/><path d="M16 12h24M16 42h24"/><circle cx="28" cy="47" r="1.5"/></svg>
      <h3>On-the-go</h3><p>Donec odio nulla, ultrices eget consequat id, blandit eu dui. Morbi accumsan lorem quis maximus mattis.</p>
    </div>
    <div class="fact">
      <svg width="56" height="56" viewBox="0 0 56 56" fill="none" stroke="#0355a3" stroke-width="2.5"><circle cx="28" cy="28" r="22"/><ellipse cx="28" cy="28" rx="10" ry="22"/><path d="M6 28h44M10 17h36M10 39h36"/></svg>
      <h3>Social connect</h3><p>Donec odio nulla, ultrices eget consequat id, blandit eu dui. Morbi accumsan lorem quis maximus mattis.</p>
    </div>
    <div class="fact">
      <svg width="56" height="56" viewBox="0 0 56 56" fill="none" stroke="#0355a3" stroke-width="2.5"><circle cx="28" cy="28" r="22"/><circle cx="28" cy="28" r="9"/><path d="M21 21l-9-9M35 21l9-9M21 35l-9 9M35 35l9 9"/></svg>
      <h3>Dedicated support</h3><p>Donec odio nulla, ultrices eget consequat id, blandit eu dui. Morbi accumsan lorem quis maximus mattis.</p>
    </div>
  </div>
</section>

<section class="pricing">
  <h2 class="title blue">PRICING</h2>
  <div class="plans">
    <div class="plan"><h3>Basic</h3><div class="price"><small>$</small>00.00<em>/month</em></div>
      <ul><li>Phasellus a velit commodo sagittis.</li><li>Aenean non vulputate erat, nec luctus est.</li><li>Aliquam fringilla quam eget</li><li>Curabitur eros felis</li></ul>
      <span class="btn-outline">Sign Up Now</span></div>
    <div class="plan"><h3>Popular</h3><div class="price"><small>$</small>00.00<em>/month</em></div>
      <ul><li>Phasellus a velit commodo sagittis.</li><li>Aenean non vulputate erat, nec luctus est.</li><li>Aliquam fringilla quam eget</li><li>Curabitur eros felis</li></ul>
      <span class="btn-outline">Sign Up Now</span></div>
    <div class="plan"><h3>Premier</h3><div class="price"><small>$</small>00.00<em>/month</em></div>
      <ul><li>Phasellus a velit commodo sagittis.</li><li>Aenean non vulputate erat, nec luctus est.</li><li>Aliquam fringilla quam eget</li><li>Curabitur eros felis</li></ul>
      <span class="btn-outline">Sign Up Now</span></div>
  </div>
</section>

<section class="reviews">
  <h2 class="title blue">SOME CUSTOMER REVIEWS</h2>
  <div class="review-list">
    <div class="review"><div class="review-card"><span class="q">“</span><p>Mauris quis sodales enim, semper ultrices massa. Pellentesque risus dolor, tristique vel facilisis at, laoreet ut elit. Fusce id augue at metus cursus pulvinar. In nec lectus porttitor, porttitor velit vel, tempus tortor.</p></div>
      <div class="reviewer"><span>Dan Morrow, <small>City name</small><span class="stars">★★★★★</span></span><div class="avatar" role="img" aria-label="Customer portrait"></div></div></div>
    <div class="review"><div class="review-card"><span class="q">“</span><p>Mauris quis sodales enim, semper ultrices massa. Pellentesque risus dolor, tristique vel facilisis at, laoreet ut elit. Fusce id augue at metus cursus pulvinar. In nec lectus porttitor, porttitor velit vel, tempus tortor.</p></div>
      <div class="reviewer"><span>Dan Morrow, <small>City name</small><span class="stars">★★★★★</span></span><div class="avatar" role="img" aria-label="Customer portrait"></div></div></div>
    <div class="review"><div class="review-card"><span class="q">“</span><p>Mauris quis sodales enim, semper ultrices massa. Pellentesque risus dolor, tristique vel facilisis at, laoreet ut elit. Fusce id augue at metus cursus pulvinar. In nec lectus porttitor, porttitor velit vel, tempus tortor.</p></div>
      <div class="reviewer"><span>Dan Morrow, <small>City name</small><span class="stars">★★★★★</span></span><div class="avatar" role="img" aria-label="Customer portrait"></div></div></div>
  </div>
  <div class="dot-row"><i class="on"></i><i></i><i></i><i></i></div>
</section>

<section class="features">
  <h2 class="title teal">FEATURES</h2>
  <div class="feature-grid">
    <div class="feature"><svg width="34" height="30" viewBox="0 0 34 30" fill="#555"><circle cx="11" cy="17" r="9"/><circle cx="11" cy="17" r="3.5" fill="#fff"/><circle cx="26" cy="8" r="6"/><circle cx="26" cy="8" r="2" fill="#fff"/></svg><div><h3>User Settings</h3><p>Donec odio nulla, ultrices eget consequat id</p></div></div>
    <div class="feature"><svg width="34" height="30" viewBox="0 0 34 30" fill="#555"><rect x="2" y="4" width="30" height="22" rx="2"/><path d="M3 6l14 11 14-11" stroke="#fff" stroke-width="2" fill="none"/></svg><div><h3>Messages Inbox</h3><p>Donec odio nulla, ultrices eget consequat id</p></div></div>
    <div class="feature"><svg width="34" height="30" viewBox="0 0 34 30" fill="#555"><circle cx="17" cy="8" r="6"/><path d="M6 28c0-8 5-12 11-12s11 4 11 12z"/><circle cx="6" cy="11" r="4"/><circle cx="28" cy="11" r="4"/><path d="M0 26c0-5 3-8 6-8v8zM34 26c0-5-3-8-6-8v8z"/></svg><div><h3>Friends List</h3><p>Donec odio nulla, ultrices eget consequat id</p></div></div>
    <div class="feature"><svg width="34" height="30" viewBox="0 0 34 30" fill="#555"><ellipse cx="13" cy="11" rx="12" ry="9"/><path d="M5 17l-3 7 8-4z"/><ellipse cx="23" cy="18" rx="10" ry="7"/><path d="M29 22l3 6-7-3z"/></svg><div><h3>Live Chat Messages</h3><p>Donec odio nulla, ultrices eget consequat id</p></div></div>
    <div class="feature"><svg width="34" height="30" viewBox="0 0 34 30" fill="#555"><rect x="3" y="4" width="28" height="24" rx="2"/><g fill="#fff"><rect x="7" y="11" width="5" height="4"/><rect x="14" y="11" width="5" height="4"/><rect x="21" y="11" width="5" height="4"/><rect x="7" y="18" width="5" height="4"/><rect x="14" y="18" width="5" height="4"/><rect x="21" y="18" width="5" height="4"/></g></svg><div><h3>Calendar / Planner</h3><p>Donec odio nulla, ultrices eget consequat id</p></div></div>
    <div class="feature"><svg width="34" height="30" viewBox="0 0 34 30" fill="#555"><path d="M17 1a9 9 0 0 0-9 9c0 7 9 19 9 19s9-12 9-19a9 9 0 0 0-9-9z"/><circle cx="17" cy="10" r="3.5" fill="#fff"/></svg><div><h3>My Places</h3><p>Donec odio nulla, ultrices eget consequat id</p></div></div>
    <div class="feature"><svg width="34" height="30" viewBox="0 0 34 30" fill="#555"><circle cx="17" cy="15" r="14"/><path d="M13 8l11 7-11 7z" fill="#fff"/></svg><div><h3>Media Player™</h3><p>Donec odio nulla, ultrices eget consequat id</p></div></div>
    <div class="feature"><svg width="34" height="30" viewBox="0 0 34 30" fill="none" stroke="#555" stroke-width="3"><circle cx="17" cy="15" r="12"/><path d="M17 15l6-6"/></svg><div><h3>Intuitive Statistics</h3><p>Donec odio nulla, ultrices eget consequat id</p></div></div>
    <div class="feature"><svg width="34" height="30" viewBox="0 0 34 30" fill="#555"><path d="M8 26a7 7 0 0 1 0-14 10 10 0 0 1 19 2 6 6 0 0 1 0 12z"/></svg><div><h3>Weather on-the-go</h3><p>Donec odio nulla, ultrices eget consequat id</p></div></div>
  </div>
</section>

<section class="functions">
  <h2 class="title teal">FUNCTIONALITYS OF THE APP</h2>
  <div class="app-shot" role="img" aria-label="Tilted white smartphone showing the shop app checkout screen"></div>
  <div class="steps">
    <div class="step"><h3>Step 1: Aenean facilisis</h3><p>Donec euismod leo lectus, id elementum elit auctor et. Vivamus sed porttitor elit. Quisque blandit ante id lorem suscipit, eu hendrerit quam rhoncus. Mauris congue ipsum gravida fermentum interdum. Phasellus in semper dui. In porttitor, diam tempus aliquam semper, libero massa tristique lacus.</p></div>
    <div class="step"><h3>Step 2: Maecenas et nulla</h3><p>Donec euismod leo lectus, id elementum elit auctor et. Vivamus sed porttitor elit. Quisque blandit ante id lorem suscipit, eu hendrerit quam rhoncus. Mauris congue ipsum gravida fermentum interdum. Phasellus in semper dui. In porttitor, diam tempus aliquam semper, libero massa tristique lacus.</p></div>
    <div class="step"><h3>Step 3: Etiam suscipit</h3><p>Donec euismod leo lectus, id elementum elit auctor et. Vivamus sed porttitor elit. Quisque blandit ante id lorem suscipit, eu hendrerit quam rhoncus. Mauris congue ipsum gravida fermentum interdum. Phasellus in semper dui. In porttitor, diam tempus aliquam semper, libero massa tristique lacus.</p></div>
  </div>
</section>

<section class="demo">
  <div class="demo-photo" role="img" aria-label="Darkened photo of a person browsing a shop on a tablet next to a wristwatch"></div>
  <div class="demo-label">DEMO</div>
  <svg class="play" width="48" height="48" viewBox="0 0 48 48"><circle cx="24" cy="24" r="23" fill="#fff"/><path d="M19 14l15 10-15 10z" fill="#333"/></svg>
</section>

<section class="screens">
  <div class="side-shot left" role="img" aria-label="Demo shop screen: product list"></div>
  <div class="side-shot right" role="img" aria-label="Demo shop screen: product detail"></div>
  <div class="phone"><div class="phone-screen" role="img" aria-label="Demo shop screen: category grid with product photos"></div><div class="phone-btn"></div></div>
  <svg class="car-arrow" style="left:133px" width="22" height="40" viewBox="0 0 22 40"><path d="M19 3L4 20l15 17" stroke="#bbb" stroke-width="3" fill="none"/></svg>
  <svg class="car-arrow" style="left:1045px" width="22" height="40" viewBox="0 0 22 40"><path d="M3 3l15 17L3 37" stroke="#bbb" stroke-width="3" fill="none"/></svg>
</section>

<section class="newsletter">
  <h2 class="title teal">NEWSLETTER</h2>
  <div class="signup"><div class="field">Name</div><div class="field">Email</div><div class="subscribe">SUBSCRIBE</div></div>
</section>

<footer class="site-footer">
  <div class="col" style="left:134px;width:230px"><h4>About Us</h4><p>Fusce posuere urna vel erat posuere gravida. Sed vestibulum nisl dolor, quis vulputate arcu dignissim in. Donec lobortis sapien eget imperdiet porta, quam ligula blandit tellus, eu fermentum felis nisl ac neque. Sed massa dolor, pharetra nec dignissim ut, tincidunt quis ipsum.</p></div>
  <div class="col" style="left:411px"><h4>Links</h4><div class="links"><ul><li>Home</li><li>About</li><li>Services</li><li>Pricing</li><li>Reviews</li></ul><ul><li>App Screens &amp; Demo</li><li>Support</li><li>Privacy Policy</li><li>Terms and conditions</li><li>Sitemap</li></ul></div></div>
  <div class="col" style="left:700px"><h4>Contact Us</h4><ul><li>12 Harbor Lane, Westfield</li><li>Phone : +1 000 555 0142</li><li>Email : support@vorbo.example</li></ul></div>
  <div class="col" style="left:977px"><h4>Social Media</h4><div class="social"><i></i><i></i><i></i></div></div>
  <div class="foot-rule"></div>
  <div class="copy">Copyright © 2016 Company name . All rights reserved.</div>
  <svg class="to-top" width="26" height="26" viewBox="0 0 26 26"><circle cx="13" cy="13" r="12" fill="#ddd"/><path d="M8 15l5-5 5 5" stroke="#777" stroke-width="2" fill="none"/></svg>
</footer>

</body>
</html>
```